Marbrook Cupcakes Website

We need a new website. We make Texas-size gourmet cupcakes and cupcake jars. We want a website similar to the one KEYlane is hosting and made. They're charging too much per month. I would like to have Blu Otter host it. see the current site at: marbrookcupcakes.com

```html
<!DOCTYPE html>
<html lang="en">
<head>
<meta charset="utf-8">
<title>Marbrook Cupcakes</title>
<link href="https://fonts.googleapis.com/css2?family=Great+Vibes&family=Lato:wght@400;700&display=swap" rel="stylesheet">
<style>
:root{
  --teal:#6ccad3;
  --teal-soft:#e2f3f5;
  --brown:#3b1b10;
  --brown-mid:#6b3a22;
  --ink:#333;
  --text:#555;
  --hero-bg:#eeeded;
  --black:#111;
  --white:#fff;
}
*{margin:0;padding:0;box-sizing:border-box}
html,body{width:1200px;height:4283px;overflow:hidden}
body{position:relative;background:var(--white);font-family:"Lato",sans-serif;color:var(--ink)}
.abs{position:absolute}
.script{font-family:"Great Vibes",cursive;font-weight:400}
.btn{position:absolute;display:flex;align-items:center;justify-content:center;background:var(--teal);color:var(--white);font-weight:700;font-size:16px;border-radius:20px;height:37px;text-decoration:none}
.nav{position:absolute;top:36px;left:392px;display:flex;gap:0;align-items:center;font-size:14px;color:#555}
.nav a{color:#555;text-decoration:none;margin-right:46px}
.nav a.active{background:var(--teal);color:var(--white);padding:4px 12px;border-radius:14px;font-weight:700}
.para{font-size:15px;line-height:24px;color:var(--text)}
.heading{font-family:"Great Vibes",cursive;font-size:54px;color:var(--brown);line-height:1}
.heading span{color:var(--teal)}
.cat-title{position:absolute;width:300px;text-align:center;font-size:26px;color:var(--brown)}
.cat-text{position:absolute;width:290px;text-align:center;font-size:14px;line-height:23px;color:var(--text)}
.photo{position:absolute;border-radius:50%}
.footer-col h3{font-size:21px;font-weight:700;color:var(--white);margin-bottom:22px}
.footer-col{position:absolute;top:3940px;color:var(--white);font-size:15px}
.footer-col ul{list-style:none}
.footer-col li{height:38.5px}
.contact-row{display:flex;gap:20px;margin-bottom:20px;line-height:25px}
</style>
</head>
<body>

<!-- HERO -->
<svg class="abs" style="left:0;top:0" width="1200" height="830" aria-hidden="true">
  <path d="M0,0H1200V690Q600,840 0,690Z" fill="var(--hero-bg)"/>
  <path d="M120,733Q600,850 1080,733" fill="none" stroke="var(--teal)" stroke-width="9"/>
  <circle cx="600" cy="765" r="320" fill="none" stroke="#d9d9d9" stroke-width="1"/>
  <path d="M243,790L243,765A357,357 0 0 1 957,765L957,790" fill="none" stroke="var(--teal)" stroke-width="3"/>
  <g fill="var(--brown)">
    <circle cx="315" cy="550" r="5"/><circle cx="395" cy="473" r="5"/><circle cx="484" cy="427" r="5"/>
    <circle cx="581" cy="408" r="5"/><circle cx="704" cy="424" r="5"/><circle cx="830" cy="492" r="5"/><circle cx="921" cy="609" r="5"/>
  </g>
  <circle cx="267" cy="637" r="6" fill="none" stroke="var(--teal)" stroke-width="2"/>
  <path id="flavorArc" d="M224,902A400,400 0 1 1 976,902" fill="none"/>
  <g font-family="Lato, sans-serif" font-size="16" fill="var(--brown)" text-anchor="middle">
    <text fill="var(--teal)"><textPath href="#flavorArc" startOffset="19%">Black Velvet</textPath></text>
    <text><textPath href="#flavorArc" startOffset="26%">Carrot Cake</textPath></text>
    <text><textPath href="#flavorArc" startOffset="34%">Red Velvet</textPath></text>
    <text><textPath href="#flavorArc" startOffset="41%">Peanut Caramel</textPath></text>
    <text><textPath href="#flavorArc" startOffset="49%">Strawberry</textPath></text>
    <text><textPath href="#flavorArc" startOffset="58%">Wedding Cake</textPath></text>
    <text><textPath href="#flavorArc" startOffset="68%">German Chocolate</textPath></text>
    <text><textPath href="#flavorArc" startOffset="79%">Chocolate Mousse</textPath></text>
  </g>
</svg>

<div class="abs" style="left:118px;top:40px;width:130px;text-align:center">
  <div style="width:52px;height:52px;border-radius:50%;background:var(--teal);margin:0 auto 8px"></div>
  <div style="font-size:15px;color:var(--teal);font-weight:700;line-height:18px">Marbrook Cupcakes</div>
</div>

<nav class="nav">
  <a class="active" href="#">Home</a><a href="#">Menu</a><a href="#">About Us</a><a href="#">Order Now</a><a href="#">Contact</a>
</nav>
<svg class="abs" style="left:900px;top:38px" width="200" height="26" aria-hidden="true">
  <circle cx="12" cy="11" r="7" fill="none" stroke="#444" stroke-width="2"/><line x1="17" y1="16" x2="23" y2="22" stroke="#444" stroke-width="2"/>
  <path d="M62,20L53,11A5,5 0 0 1 62,6A5,5 0 0 1 71,11Z" fill="none" stroke="#444" stroke-width="2"/>
  <circle cx="73" cy="5" r="4" fill="var(--teal)"/>
  <path d="M102,5H107L110,17H122L125,9H108" fill="none" stroke="#444" stroke-width="2"/>
  <circle cx="112" cy="22" r="2" fill="#444"/><circle cx="121" cy="22" r="2" fill="#444"/>
  <text x="136" y="17" font-family="Lato, sans-serif" font-size="13" fill="#444">0 / $0.00</text>
</svg>

<h1 class="abs script" style="left:0;width:1200px;top:105px;text-align:center;font-size:72px;color:var(--teal);line-height:1">Marbrook Cupcakes</h1>
<p class="abs" style="left:0;width:1200px;top:200px;text-align:center;font-size:20px;line-height:25px;color:#333">Freshly Baked, Gourmet Cupcakes &amp; Cupcake<br>Jars, Crafted with Love</p>
<a class="btn" href="#" style="left:523px;top:272px;width:154px">Order Now</a>

<div class="abs" role="img" aria-label="Chocolate frosted cupcake" style="left:415px;top:470px;width:370px;height:315px;border-radius:48% 48% 20% 20%;background:radial-gradient(circle at 50% 35%,#c08a6a,#7a4a30 60%,#3a2218)"></div>
<div class="abs" role="img" aria-label="Swirl lollipop" style="left:40px;top:275px;width:110px;height:95px;border-radius:50%;background:radial-gradient(circle,#f7c7d6,#bfe4ee)"></div>
<div class="abs" role="img" aria-label="Chocolate splash with chocolate chunks" style="left:905px;top:175px;width:200px;height:165px;border-radius:50%;background:radial-gradient(circle,#6b3a22,rgba(107,58,34,0) 70%)"></div>
<div class="abs" role="img" aria-label="Whisk dripping chocolate" style="left:5px;top:505px;width:120px;height:190px;background:linear-gradient(160deg,rgba(150,150,150,.4),rgba(90,50,30,.5))"></div>

<!-- ABOUT -->
<svg class="abs" style="left:100px;top:880px" width="500" height="520" aria-hidden="true">
  <path d="M12,255A241,241 0 0 0 470,320" fill="none" stroke="var(--teal)" stroke-width="12"/>
</svg>
<div class="photo" role="img" aria-label="Portrait of the owner in a dark suit" style="left:113px;top:894px;width:482px;height:482px;background:radial-gradient(circle at 50% 40%,#d9d9d9,#8a8a8a)"></div>
<h2 class="abs heading" style="left:693px;top:955px">About <span>Us</span></h2>
<p class="abs para" style="left:695px;top:1031px;width:390px">Lorem ipsum dolor sit amet, consectetur adipiscing elit, sed do eiusmod tempor incididunt ut labore et dolore magna aliqua. Ut enim ad minim veniam, quis nostrud exercitation ullamco laboris nisi ut aliquip ex ea commodo consequat. Duis aute irure dolor in reprehenderit in voluptate velit esse cillum dolore eu fugiat nulla pariatur. Excepteur sint occaecat cupidatat non proident, sunt in culpa qui officia deserunt mollit anim id est laborum.</p>
<a class="btn" href="#" style="left:695px;top:1254px;width:155px">Order Now</a>

<!-- CATEGORIES -->
<svg class="abs" style="left:0;top:1470px" width="1200" height="1000" aria-hidden="true">
  <path d="M0,60Q60,20 120,60T240,50T360,40Q420,-10 480,40T620,30T760,50T900,30T1040,50T1200,30V890Q1140,930 1080,900T960,940T840,910T720,950T600,920T480,960T360,920T240,950T120,920T0,940Z" fill="var(--teal-soft)"/>
</svg>
<h2 class="abs heading" style="left:0;width:1200px;text-align:center;top:1608px">Our <span>Categories</span></h2>
<p class="abs" style="left:0;width:1200px;top:1676px;text-align:center;font-size:16px;line-height:24px;color:#444">From Texas-sized gourmet cupcakes to on-the-go cupcake jars, custom orders,<br>and more—find your perfect treat below!</p>

<div class="photo" role="img" aria-label="Wedding cake cupcake with white frosting" style="left:111px;top:1778px;width:350px;height:350px;background:radial-gradient(circle at 50% 40%,#f3eee2,#a8643a 70%)"></div>
<div class="photo" role="img" aria-label="Red velvet cupcake with cream cheese frosting" style="left:742px;top:1778px;width:350px;height:350px;background:radial-gradient(circle at 50% 40%,#f4efe6,#9a2a25 55%,#8a4a2c)"></div>
<div class="photo" role="img" aria-label="Strawberry cupcake topped with fresh strawberry" style="left:402px;top:1745px;width:392px;height:392px;border:4px solid var(--white);background:radial-gradient(circle at 50% 35%,#f6dcd2,#d98a4a 55%,#7a4a2c)"></div>

<svg class="abs" style="left:52px;top:1938px" width="36" height="36" aria-hidden="true"><circle cx="18" cy="18" r="17" fill="var(--brown)"/><path d="M21,11L14,18L21,25" fill="none" stroke="#fff" stroke-width="3"/></svg>
<svg class="abs" style="left:1112px;top:1938px" width="36" height="36" aria-hidden="true"><circle cx="18" cy="18" r="17" fill="var(--brown)"/><path d="M15,11L22,18L15,25" fill="none" stroke="#fff" stroke-width="3"/></svg>

<h3 class="cat-title" style="left:136px;top:2176px">Wedding Cake</h3>
<h3 class="cat-title" style="left:452px;top:2176px">Strawberry</h3>
<h3 class="cat-title" style="left:767px;top:2176px">Red Velvet</h3>
<p class="cat-text" style="left:141px;top:2222px">Lorem ipsum dolor sit amet, consectetur adipiscing elit, sed do eiusmod tempor incididunt ut labore et dolore aliqua.</p>
<p class="cat-text" style="left:457px;top:2222px">Lorem ipsum dolor sit amet, consectetur adipiscing elit, sed do eiusmod tempor incididunt ut labore et dolore aliqua.</p>
<p class="cat-text" style="left:772px;top:2222px">Lorem ipsum dolor sit amet, consectetur adipiscing elit, sed do eiusmod tempor incididunt ut labore et dolore aliqua.</p>
<a class="btn" href="#" style="left:523px;top:2310px;width:154px">Order Now</a>

<!-- WHY CHOOSE US -->
<h2 class="abs heading" style="left:111px;top:2608px">Why Choose <span>Us</span></h2>
<p class="abs para" style="left:111px;top:2684px;width:395px">Lorem ipsum dolor sit amet, consectetur adipiscing elit, sed do eiusmod tempor incididunt ut labore et dolore magna aliqua. Ut enim ad minim veniam, quis nostrud exercitation ullamco laboris nisi ut aliquip ex ea commodo consequat. Duis aute irure dolor in reprehenderit in voluptate velit esse cillum dolore eu fugiat nulla pariatur. Excepteur sint occaecat cupidatat non proident, sunt in culpa qui officia deserunt mollit anim id est laborum.</p>
<a class="btn" href="#" style="left:113px;top:2909px;width:154px">Order Now</a>
<svg class="abs" style="left:590px;top:2540px" width="520" height="520" aria-hidden="true">
  <path d="M500,230A244,244 0 0 1 180,500" fill="none" stroke="var(--brown)" stroke-width="12"/>
</svg>
<div class="photo" role="img" aria-label="German chocolate cupcakes on glass stands" style="left:604px;top:2548px;width:488px;height:488px;background:radial-gradient(circle at 45% 40%,#c9955e,#7a4328 60%,#4a2616)"></div>

<!-- TESTIMONIAL -->
<div class="abs" role="img" aria-label="Teal tinted photo of cupcakes" style="left:60px;top:3116px;width:1080px;height:404px;border-radius:202px;background:linear-gradient(90deg,#62c1cb,#74cdd5 50%,#62c1cb)"></div>
<h2 class="abs heading" style="left:0;width:1200px;text-align:center;top:3200px;font-size:50px">What Our Customers Are Saying</h2>
<div class="abs" style="left:196px;top:3252px;font-size:64px;color:var(--white);font-family:Georgia,serif;line-height:1">“</div>
<p class="abs" style="left:230px;top:3276px;width:740px;text-align:center;font-size:18px;line-height:25px;color:var(--white)">Lorem ipsum dolor sit amet, consectetur adipiscing elit, sed do eiusmod tempor incididunt ut labore et dolore magna aliqua. Ut enim ad minim veniam, quis nostrud exercitation ullamco laboris nisi ut aliquip ex ea commodo consequat.</p>
<div class="abs" style="left:830px;top:3330px;font-size:64px;color:var(--white);font-family:Georgia,serif;line-height:1">”</div>
<p class="abs" style="left:0;width:1200px;text-align:center;top:3365px;font-size:19px;color:var(--brown)">Dana M.</p>
<svg class="abs" style="left:558px;top:3425px" width="84" height="10" aria-hidden="true"><rect x="0" y="0" width="22" height="7" fill="#fff"/><rect x="30" y="0" width="22" height="7" fill="#fff"/><rect x="60" y="0" width="22" height="7" fill="#fff"/></svg>

<!-- FOOTER -->
<svg class="abs" style="left:0;top:3560px" width="1200" height="723" aria-hidden="true">
  <path d="M0,165Q600,20 1200,165V723H0Z" fill="var(--black)"/>
  <path d="M130,110Q600,5 1070,110" fill="none" stroke="var(--teal)" stroke-width="10"/>
  <line x1="111" y1="678" x2="1090" y2="678" stroke="#333" stroke-width="1"/>
</svg>
<div class="abs" style="left:0;width:1200px;top:3740px;text-align:center;font-size:72px;color:var(--teal);line-height:1">Marbrook Cupcakes</div>

<div class="footer-col" style="left:111px;width:240px">
  <h3>About Us</h3>
  <p style="font-size:14px;line-height:25px">Excepteur sint occaecat cupidatat non proident, sunt in culpa qui officia deserunt mollit anim id est laborum.</p>
  <svg style="margin-top:26px" width="190" height="40" aria-label="Social links" role="img">
    <rect x="2" y="2" width="36" height="36" rx="6" fill="var(--teal)"/>
    <rect x="59" y="10" width="20" height="20" rx="5" fill="none" stroke="#fff" stroke-width="2"/>
    <rect x="106" y="10" width="20" height="20" rx="2" fill="none" stroke="#fff" stroke-width="2"/>
    <rect x="151" y="12" width="24" height="17" rx="4" fill="none" stroke="#fff" stroke-width="2"/>
  </svg>
</div>
<div class="footer-col" style="left:415px">
  <h3>Main Links</h3>
  <ul><li>Home</li><li>Menu</li><li>About Us</li><li>Order Now</li><li>Contact Us</li></ul>
</div>
<div class="footer-col" style="left:630px;width:290px">
  <h3>Contact Us</h3>
  <div class="contact-row"><svg width="18" height="24" aria-hidden="true"><path d="M9,22C3,14 2,11 2,8A7,7 0 0 1 16,8C16,11 15,14 9,22Z" fill="none" stroke="#fff" stroke-width="1.5"/><circle cx="9" cy="8" r="2.5" fill="none" stroke="#fff" stroke-width="1.5"/></svg><span>123, Marbrook Cupcakes<br>Company Na,12345.</span></div>
  <div class="contact-row" style="margin-top:32px"><svg width="18" height="24" aria-hidden="true"><path d="M3,4L7,3L9,8L7,10Q9,14 12,16L14,14L18,16L17,20Q9,20 3,4Z" fill="none" stroke="#fff" stroke-width="1.5"/></svg><span>+ 1 555 014 2290</span></div>
  <div class="contact-row" style="margin-top:32px"><svg width="18" height="24" aria-hidden="true"><rect x="1" y="6" width="17" height="12" fill="none" stroke="#fff" stroke-width="1.5"/><path d="M1,6L9.5,13L18,6" fill="none" stroke="#fff" stroke-width="1.5"/></svg><span>info@marbrookcupcakes.com</span></div>
</div>
<div class="footer-col" style="left:956px">
  <h3>Main Links</h3>
  <ul><li>Help</li><li>Support</li><li>Cookies Policy</li><li>Terms &amp; Conditions</li><li>Privacy Policy</li></ul>
</div>
<p class="abs" style="left:0;width:1200px;text-align:center;top:4252px;font-size:13px;color:var(--white)">Copyright © 2025 Marbrook Cupcakes. All rights reserved.</p>

</body>
</html>
```